Business Card Design Project

We need a business card for a new technology services company. We develop software and implement software packages for our business customers and although we will begin with just one or two service offerings, our service offerings will expand over time. Our name comes from the an author, KL Barrow, and his "idea" was that opportunity should be based on ability and achievement, not on social status.

We would like to see a design that is standard in its size and shape, but stands apart in its dramatic color contrasts. The card should not use too many colors - the colors used in the background should highlight the brilliant blues of the logo (see attachment) to dramatic effect. The background should not be white.

If necessary, you can change the color of the words "KL Barrow", but not the word "Idea".

Card size should be U.S. standard 2 inches by 3.5 inches and provide for 1/8 inch bleed area on each side.

We need a design for both sides of the business card, one side communicating the company logo and contact information, the other side being purely graphical, incorporating the logo but no other information.

Contact Information Required:
Kate Brook
KateBrook@klbarrowvista.com
614-387-2259

Target Market(s)

Business executives

Industry/Entity Type

Software

Requirements
Must have
• It must have the full company logo on one side, and at least the graphic element of the logo on the other. Either that or the full logo on both.
Nice to have
• It would be nice to have a design that could work without needing two different textures. For example, it would be nice if the entire card could be shiny, not just parts of the card.

It would also be nice if texture is something we could add later.
Should not have
• The card should not use the color green.

```html
<!DOCTYPE html>
<html lang="en">
<head>
<meta charset="utf-8">
<title>KL Barrow Vista – Business Card</title>
<link rel="stylesheet" href="https://fonts.googleapis.com/css2?family=Arimo:wght@400;700&display=swap">
<style>
  :root {
    --page-bg: #e9e6e1;
    --card-dark: #151515;
    --card-mid: #2e2e2e;
    --brand-blue: #1c9ad8;
    --text-soft: #bdbdbd;
    --text-white: #ffffff;
  }
  * { margin: 0; padding: 0; box-sizing: border-box; }
  html, body { width: 1200px; height: 720px; overflow: hidden; }
  body {
    background: var(--page-bg);
    font-family: "Arimo", Arial, sans-serif;
    position: relative;
  }
  .card {
    position: absolute;
    top: 205px;
    width: 540px;
    height: 309px;
    border-radius: 4px;
    overflow: hidden;
    box-shadow: 0 6px 18px rgba(0,0,0,0.25);
  }
  .card--contact { left: 40px; }
  .card--graphic { left: 620px; }
  .card__surface {
    position: absolute; inset: 0;
    background: radial-gradient(ellipse at 62% 40%, var(--card-mid) 0%, var(--card-dark) 70%);
  }
  .edge-stripe {
    position: absolute;
    top: 0; bottom: 0; right: 0;
    width: 10px;
    background: var(--brand-blue);
  }
  .holder {
    position: absolute;
    top: 28px; right: 40px;
    text-align: right;
  }
  .holder__name {
    color: var(--text-white);
    font-weight: 700;
    font-size: 17px;
    letter-spacing: 1px;
  }
  .holder__rule {
    display: block;
    margin: 8px 0 0 auto;
    width: 48px; height: 2px;
    background: var(--brand-blue);
  }
  .brand {
    position: absolute;
    display: flex;
    align-items: center;
    gap: 12px;
    color: var(--text-white);
    font-weight: 700;
    letter-spacing: 0;
    white-space: nowrap;
  }
  .brand__mark { background: var(--brand-blue); flex: none; }
  .card--contact .brand { left: 28px; top: 166px; font-size: 28px; }
  .card--contact .brand__mark { width: 14px; height: 14px; }
  .card--graphic .brand { left: 100px; top: 150px; font-size: 40px; }
  .card--graphic .brand__mark { width: 20px; height: 20px; }
  .contact-list {
    position: absolute;
    left: 28px; top: 232px;
    list-style: none;
    color: var(--text-soft);
    font-size: 13px;
    letter-spacing: 0.4px;
  }
  .contact-list li { display: flex; align-items: center; gap: 8px; margin-bottom: 9px; }
  .contact-list svg { width: 11px; height: 11px; flex: none; }
  .icon-phone { fill: var(--brand-blue); }
  .icon-mail { fill: none; stroke: var(--brand-blue); stroke-width: 2; }
</style>
</head>
<body>

  <section class="card card--contact" aria-label="Contact side">
    <div class="card__surface" role="img" aria-label="Dark brushed wood grain texture"></div>
    <span class="edge-stripe" aria-hidden="true"></span>
    <div class="holder">
      <p class="holder__name">KATE BROOK</p>
      <span class="holder__rule" aria-hidden="true"></span>
    </div>

    <div class="brand">
      <span class="brand__mark" aria-hidden="true"></span>
      <span class="brand__name">KL Barrow Vista</span>
    </div>

    <ul class="contact-list">
      <li>
        <svg class="icon-phone" viewBox="0 0 24 24" aria-hidden="true"><path d="M6.6 10.8a15 15 0 0 0 6.6 6.6l2.2-2.2a1 1 0 0 1 1-.25 11.4 11.4 0 0 0 3.6.57 1 1 0 0 1 1 1V20a1 1 0 0 1-1 1A17 17 0 0 1 3 4a1 1 0 0 1 1-1h3.5a1 1 0 0 1 1 1c0 1.25.2 2.45.57 3.57a1 1 0 0 1-.25 1z"/></svg>
        <span>614-387-2259</span>
      </li>
      <li>
        <svg class="icon-mail" viewBox="0 0 24 24" aria-hidden="true"><path d="M3 6h18v12H3z M3 6l9 7 9-7"/></svg>
        <span>KateBrook@klbarrowvista.com</span>
      </li>
    </ul>
  </section>

  <section class="card card--graphic" aria-label="Logo side">
    <div class="card__surface" role="img" aria-label="Dark brushed wood grain texture"></div>
    <span class="edge-stripe" aria-hidden="true"></span>
    <div class="brand">
      <span class="brand__mark" aria-hidden="true"></span>
      <span class="brand__name">KL Barrow Vista</span>
    </div>
  </section>

</body>
</html>
```